Brell Stone Company Business Cards

Front and Back Business Card - logo and text setup - cool design. I need workable photoshop or illustrator files so I can setup each employee card with design that is created
Updates

Hi everyone, thank you for the great entries. Please no more white and blue cards - there are so many already - black and silver only now please. thanks!

Target Market(s)

Construction Industry - Facility Managers

Industry/Entity Type

Construction

Contact Information for Business Card

I really like contemporary simplistic looks - clean neat....not opposed to seeing some black backrounds

Requirements
Must have
• Logo/website address with design on front only - www.brellstone-example.com (logo attached)
• Back:
• Name/Title/Company Address/Phone/email address
Nice to have
• Cool design
Should not have
• Nothing gimmicky like Fire or Water - since we are a Fire Protection company - it has all been done

```html
<!DOCTYPE html>
<html lang="en">
<head>
<meta charset="utf-8">
<title>Brell Stone Company — Business Cards</title>
<link rel="stylesheet" href="https://fonts.googleapis.com/css2?family=PT+Sans:ital,wght@0,400;0,700;1,400;1,700&display=swap">
<style>
  :root {
    --backdrop: #c8cacc;
    --card-black: #000000;
    --brand-blue: #0323a0;
    --brand-red: #ff2020;
    --white: #ffffff;
  }
  * { box-sizing: border-box; margin: 0; padding: 0; }
  html, body {
    width: 1200px; height: 1193px; overflow: hidden;
    background: var(--backdrop);
    font-family: "PT Sans", sans-serif;
  }
  .sheet { position: relative; width: 1200px; height: 1193px; }
  .card {
    position: absolute; width: 873px; height: 499px;
    background: var(--card-black); border-radius: 22px; overflow: hidden;
    color: var(--white);
  }
  .card--front { left: 62px; top: 71px; }
  .card--back { left: 263px; top: 617px; }

  .contact-band {
    position: absolute; left: 0; right: 0; bottom: 0; height: 196px;
    background: var(--brand-blue);
    border-top: 6px solid var(--brand-red);
  }
  .contact-band::before {
    content: ""; position: absolute; left: 0; right: 0; top: 4px;
    height: 3px; background: var(--white);
  }

  .wordmark {
    position: absolute; font-weight: 700; color: var(--brand-red);
    white-space: nowrap; letter-spacing: -0.5px;
  }
  .card--front .wordmark { left: 44px; top: 122px; font-size: 48px; line-height: 1; }
  .card--back .wordmark { left: 0; right: 0; top: 196px; text-align: center; font-size: 58px; line-height: 1; }
  .back-url {
    position: absolute; left: 0; right: 0; top: 312px; text-align: center;
    font-size: 25px; letter-spacing: 4px;
  }
  .person { position: absolute; right: 29px; top: 38px; text-align: right; font-style: italic; font-weight: 700; }
  .person__name { font-size: 30px; line-height: 36px; }
  .person__title { font-size: 25px; line-height: 32px; }
  .address { position: absolute; left: 40px; top: 402px; font-size: 23px; line-height: 34px; font-style: normal; }
  .contacts { position: absolute; right: 29px; top: 352px; list-style: none; font-size: 22px; }
  .contacts li { display: flex; align-items: center; justify-content: flex-end; gap: 14px; height: 38px; }
  .contacts svg { width: 23px; height: 23px; flex: none; }
</style>
</head>
<body>
<main class="sheet">
  <section class="card card--front" aria-label="Business card front">
    <div class="contact-band" aria-hidden="true"></div>
    <div class="wordmark">Brell Stone Company</div>
    <div class="person">
      <p class="person__name">Dana Whitfield</p>
      <p class="person__title">President</p>
    </div>
    <address class="address">
      <p>48 Meridian Way</p>
      <p>Harbor Falls, NY 10099</p>
    </address>
    <ul class="contacts">
      <li><span>(555) 014-2290</span>
        <svg viewBox="0 0 24 24" aria-hidden="true"><path d="M6.5 2.5l3 4-2 2.2c1.2 2.8 3.2 4.9 6 6.2l2.2-2 4 3-2 3.6C10.5 19 4.8 13.3 3 5.2z" fill="var(--white)"/></svg></li>
      <li><span>info@brellstone-example.com</span>
        <svg viewBox="0 0 24 24" aria-hidden="true"><rect x="2" y="5" width="20" height="14" fill="var(--white)"/><path d="M2 5l10 8 10-8M2 19l7-7M22 19l-7-7" fill="none" stroke="var(--brand-blue)" stroke-width="1.8"/></svg></li>
      <li><span>www.brellstone-example.com</span>
        <svg viewBox="0 0 24 24" aria-hidden="true" fill="none" stroke="var(--white)" stroke-width="1.6"><circle cx="12" cy="12" r="10"/><ellipse cx="12" cy="12" rx="4.5" ry="10"/><path d="M2 12h20M4 6.5h16M4 17.5h16M12 2v20"/></svg></li>
    </ul>
  </section>

  <section class="card card--back" aria-label="Business card back">
    <div class="wordmark">Brell Stone Company</div>
    <p class="back-url">www.brellstone-example.com</p>
  </section>
</main>
</body>
</html>
```